Design and Renovation Company Luxury Business Card

I want to create a luxury business card for a Design and Renovation Firm . We will use our current logo. The company name is 528BUILDA. We do not want anything standard. We need a very unique concept.
Please see uploaded inspiration. I really like the textured paper option. I would like the card to be thick with debossing, and/or embossing options. The logo has orange in it but I would like to see the card with and without the orange. I think the orange may make the company feel less high-end. The goal is to elevate the logo not match its vibe per se of the logo. We want something very unique, not standard at all!
I would like a space for :
Logo,
Name,
Position,
Email,
Office number,
Website Address,
Business Address,
Thank you!
Have fun!
Target Market(s)
Home owners Age 35 +
Industry/Entity Type
Design and Renovation
Contact Information for Business Card
Logo, Name, Position, Email, Office number, Website Address, Business Address,.
Colors
Designer to choose colors to be used in the design.
Requirements
Must have
- A luxury designer feel. Must be black or dark grey but open to other luxury ideas.
Nice to have
- Gold, silver, black embossing or debossing. Textured paper design.
Should not have
- A cheap look and feel.

```html
<!DOCTYPE html>
<html lang="en">
<head>
<meta charset="utf-8">
<title>528BUILDA Business Card</title>
<link href="https://fonts.googleapis.com/css2?family=Montserrat:wght@400;500;600&display=swap" rel="stylesheet">
<style>
  :root {
    --backdrop: #161616;
    --card: #262626;
    --card-edge: #303030;
    --silver: #c9c9c9;
    --ink-light: #f2f2f2;
    --rule: #bdbdbd;
  }
  * { margin: 0; padding: 0; box-sizing: border-box; }
  html, body {
    width: 1200px;
    height: 1063px;
    overflow: hidden;
    background: var(--backdrop);
    font-family: "Montserrat", sans-serif;
  }
  .stage {
    position: relative;
    width: 1200px;
    height: 1063px;
  }
  .card {
    position: absolute;
    width: 760px;
    height: 434px;
    background: var(--card);
    border: 1px solid var(--card-edge);
    box-shadow: 0 18px 40px rgba(0,0,0,0.55);
  }
  .card--front { left: 300px; top: 90px; }
  .card--back { left: 160px; top: 545px; }

  /* Front */
  .brand-name {
    position: absolute;
    left: 0; right: 0;
    top: 180px;
    text-align: center;
    font-weight: 500;
    font-size: 64px;
    letter-spacing: 8px;
    line-height: 1;
    color: var(--silver);
  }

  /* Back */
  .person {
    position: absolute;
    right: 405px;
    top: 218px;
    text-align: right;
    color: var(--ink-light);
  }
  .person__name {
    font-weight: 500;
    font-size: 30px;
    letter-spacing: 1.5px;
    line-height: 1.1;
  }
  .person__role {
    font-weight: 600;
    font-size: 17px;
    margin-top: 4px;
  }
  .divider {
    position: absolute;
    left: 372px;
    top: 200px;
    width: 1px;
    height: 150px;
    background: var(--rule);
  }
  .contact {
    position: absolute;
    left: 392px;
    top: 200px;
    color: var(--ink-light);
    font-size: 19px;
    line-height: 1.3;
  }
  .contact__address { margin-bottom: 8px; }
  .contact__row {
    display: flex;
    align-items: center;
    gap: 10px;
  }
  .contact__icon {
    width: 16px;
    height: 16px;
    flex: none;
    fill: none;
    stroke: var(--ink-light);
    stroke-width: 1.6;
  }
</style>
</head>
<body>
<main class="stage">
  <section class="card card--front" aria-label="Card front">
    <div class="brand-name">528BUILDA</div>
  </section>

  <section class="card card--back" aria-label="Card back">
    <div class="person">
      <div class="person__name">DANIEL MERCER</div>
      <div class="person__role">President</div>
    </div>
    <div class="divider"></div>
    <div class="contact">
      <div class="contact__address">4412 Alder Court<br>Kelowna, Canada 56120</div>
      <div class="contact__row">
        <svg class="contact__icon" viewBox="0 0 16 16" aria-hidden="true">
          <path d="M4 1.5l2.5 3-1.5 1.8c.9 1.9 2.3 3.3 4.2 4.2l1.8-1.5 3 2.5-1.5 2.5C7 13.5 2.5 9 1.5 3z"/>
        </svg>
        <span>604-218-7390</span>
      </div>
      <div class="contact__row">
        <svg class="contact__icon" viewBox="0 0 16 16" aria-hidden="true">
          <rect x="1.5" y="3.5" width="13" height="9"/>
          <path d="M1.5 3.5l6.5 5 6.5-5"/>
        </svg>
        <span>info@528builda.com</span>
      </div>
      <div class="contact__row">
        <svg class="contact__icon" viewBox="0 0 16 16" aria-hidden="true">
          <circle cx="8" cy="8" r="6.5"/>
          <path d="M1.5 8h13M8 1.5c-2.5 3-2.5 10 0 13M8 1.5c2.5 3 2.5 10 0 13"/>
        </svg>
        <span>www.528builda.com</span>
      </div>
    </div>
  </section>
</main>
</body>
</html>
```